Flyer for the Lumen 2025 Conference

I am looking to produce a flyer for our upcoming conference, Lumen 2025. This is an annual conference that we plan to publicize on social media. The ideal designer will create a flyer that is eye-catching and effectively communicates the key information. Please see attached our logo, speaker photo, and flyer content.

Target Market(s)

All demographics

Industry/Entity Type

Christian

Font styles to use
Sans Serif

Requirements
Should not have
• Cross, church

```html
<!DOCTYPE html>
<html lang="en">
<head>
<meta charset="utf-8">
<title>Lumen 2025 Conference Flyer</title>
<link rel="stylesheet" href="https://fonts.googleapis.com/css2?family=Bebas+Neue&family=Montserrat:wght@500;600;700;800&family=Allura&display=swap">
<style>
  :root {
    --stage: #c9c9cb;
    --ink: #000000;
    --navy: #1f1c6b;
    --navy-deep: #0b0a2e;
    --orange: #f5a01e;
    --orange-deep: #e0741c;
    --teal: #4cc3d1;
    --white: #ffffff;
  }
  * { margin: 0; padding: 0; box-sizing: border-box; }
  html, body { width: 911px; height: 1200px; overflow: hidden; background: var(--stage); }
  .canvas { position: relative; width: 911px; height: 1200px; }
  .flyer {
    position: absolute; left: 91px; top: 85px; width: 728px; height: 1030px; overflow: hidden;
    background: radial-gradient(ellipse 70% 55% at 60% 50%, var(--navy) 0%, var(--navy-deep) 60%, var(--ink) 100%);
    font-family: "Montserrat", sans-serif; color: var(--white);
  }
  .flyer > * { position: absolute; }
  .speaker-photo {
    left: 0; top: 197px; width: 440px; height: 634px;
    background: radial-gradient(ellipse 60% 70% at 40% 45%, #2f6fc4 0%, #1b3f8a 45%, rgba(11,10,46,0) 80%);
  }
  .brand { left: 53px; top: 88px; display: flex; align-items: center; gap: 10px; }
  .brand-dot { width: 22px; height: 22px; border-radius: 50%; background: var(--orange); }
  .brand-name { font-weight: 700; font-size: 46px; letter-spacing: 1px; color: var(--white); line-height: 1; }
  .speaker { right: 42px; top: 28px; text-align: right; line-height: 1.05; }
  .speaker-label { color: var(--orange); font-weight: 800; font-size: 22px; }
  .speaker-name { font-weight: 600; font-size: 22px; }
  .title { font-family: "Bebas Neue", sans-serif; line-height: 0.8; white-space: nowrap; }
  .title-name {
    left: 296px; top: 190px; font-size: 182px; letter-spacing: 2px;
    background: linear-gradient(180deg, var(--orange-deep), var(--orange) 60%, #e88a1c);
    -webkit-background-clip: text; background-clip: text; color: transparent;
  }
  .title-year { left: 296px; top: 330px; font-size: 262px; letter-spacing: -6px; color: var(--white); }
  .title-tag { left: 294px; top: 542px; font-size: 106px; letter-spacing: -1px; color: var(--teal); }
  .title-kind { left: 295px; top: 636px; font-weight: 600; font-size: 52px; letter-spacing: 0; line-height: 1; }
  .venue { right: 32px; top: 700px; text-align: right; }
  .venue-label { font-family: "Allura", cursive; color: var(--orange); font-size: 42px; line-height: 1; }
  .venue-name { font-weight: 800; font-size: 15.5px; margin-top: 2px; }
  .venue-address { font-weight: 500; font-size: 15px; margin-top: 2px; }
  .day {
    top: 831px; width: 118px; height: 160px; border: 2px solid var(--orange);
    background: var(--ink); text-align: center;
  }
  .day-1 { left: 42px; } .day-2 { left: 182px; } .day-3 { left: 322px; }
  .day-month { font-family: "Bebas Neue", sans-serif; color: var(--teal); font-size: 27px; line-height: 1; margin-top: 10px; }
  .day-date { font-family: "Bebas Neue", sans-serif; font-size: 58px; line-height: 0.85; margin-top: 2px; }
  .day-weekday { color: var(--orange); font-weight: 800; font-size: 19px; line-height: 1; margin-top: 3px; }
  .day-time { position: relative; width: 83px; margin: 5px auto 0; }
  .time-bar { display: block; height: 18px; font-weight: 700; font-size: 15px; line-height: 18px; color: var(--white); }
  .time-start { background: var(--orange); }
  .time-end { background: var(--teal); margin-top: 4px; }
  .time-to {
    position: absolute; left: 50%; top: 15px; transform: translateX(-50%);
    width: 10px; height: 10px; border-radius: 50%; background: var(--white); color: var(--ink);
    font-size: 5px; font-weight: 800; line-height: 10px;
  }
  .app { left: 466px; top: 830px; line-height: 1.2; }
  .app-lead { font-weight: 500; font-size: 15px; }
  .app-name { color: var(--orange); font-weight: 800; font-size: 22px; line-height: 1.1; }
  .app-note { font-weight: 500; font-size: 14px; }
  .stores { display: flex; gap: 6px; margin-top: 6px; }
  .store-badge { width: 81px; height: 25px; border-radius: 4px; background: var(--white); }
  .contacts { left: 466px; top: 1012px - 85px; list-style: none; }
  .contact-list { left: 466px; top: 932px; list-style: none; }
  .contact-item { display: flex; align-items: center; gap: 6px; height: 21px; font-weight: 600; font-size: 15px; }
  .contact-icon { width: 16px; height: 16px; flex: none; }
</style>
</head>
<body>
<div class="canvas">
  <main class="flyer">
    <div class="speaker-photo" role="img" aria-label="Portrait of the speaker in a blue suit, seated"></div>

    <div class="brand">
      <span class="brand-dot"></span>
      <span class="brand-name">KAVRE</span>
    </div>

    <div class="speaker">
      <div class="speaker-label">SPEAKER:</div>
      <div class="speaker-name">PROPHET SAMUEL OKORO</div>
    </div>

    <h1 class="title title-name">LUMEN</h1>
    <div class="title title-year">2025</div>
    <div class="title title-tag">A PROPHETIC</div>
    <div class="title-kind">CONFERENCE</div>

    <div class="venue">
      <div class="venue-label">Location</div>
      <div class="venue-name">The Riverside Performing Arts Center</div>
      <div class="venue-address">218 Maplewood Avenue Brookfield, Maine 04180</div>
    </div>

    <div class="day day-1">
      <div class="day-month">DECEMBER</div>
      <div class="day-date">26TH</div>
      <div class="day-weekday">FRIDAY</div>
      <div class="day-time"><span class="time-bar time-start">6:30 PM</span><span class="time-to">TO</span><span class="time-bar time-end">9:00 PM</span></div>
    </div>
    <div class="day day-2">
      <div class="day-month">DECEMBER</div>
      <div class="day-date">27TH</div>
      <div class="day-weekday">SATURDAY</div>
      <div class="day-time"><span class="time-bar time-start">5:30 PM</span><span class="time-to">TO</span><span class="time-bar time-end">8:00 PM</span></div>
    </div>
    <div class="day day-3">
      <div class="day-month">DECEMBER</div>
      <div class="day-date">29TH</div>
      <div class="day-weekday">SUNDAY</div>
      <div class="day-time"><span class="time-bar time-start">4:30 PM</span><span class="time-to">TO</span><span class="time-bar time-end">7:00 PM</span></div>
    </div>

    <div class="app">
      <div class="app-lead">Download the</div>
      <div class="app-name">KAVRE APP</div>
      <div class="app-note">to stay updated on the event</div>
      <div class="stores">
        <span class="store-badge"></span>
        <span class="store-badge"></span>
      </div>
    </div>

    <ul class="contact-list">
      <li class="contact-item">
        <svg class="contact-icon" viewBox="0 0 16 16" aria-hidden="true"><circle cx="8" cy="8" r="8" fill="#f5a01e"/><rect x="5.5" y="3.5" width="5" height="9" rx="1" fill="none" stroke="#000" stroke-width="1"/><line x1="7.2" y1="11" x2="8.8" y2="11" stroke="#000" stroke-width="0.8"/></svg>
        <span>207 555 0183</span>
      </li>
      <li class="contact-item">
        <svg class="contact-icon" viewBox="0 0 16 16" aria-hidden="true"><circle cx="8" cy="8" r="8" fill="#f5a01e"/><rect x="4" y="5" width="8" height="6" rx="0.8" fill="none" stroke="#000" stroke-width="1"/><polyline points="4,5.4 8,8.5 12,5.4" fill="none" stroke="#000" stroke-width="1"/></svg>
        <span>contact@kavre.org</span>
      </li>
      <li class="contact-item">
        <svg class="contact-icon" viewBox="0 0 16 16" aria-hidden="true"><circle cx="8" cy="8" r="8" fill="#f5a01e"/><circle cx="8" cy="8" r="4.2" fill="none" stroke="#000" stroke-width="0.9"/><ellipse cx="8" cy="8" rx="1.8" ry="4.2" fill="none" stroke="#000" stroke-width="0.8"/><line x1="3.8" y1="8" x2="12.2" y2="8" stroke="#000" stroke-width="0.8"/></svg>
        <span>www.kavre.org</span>
      </li>
    </ul>
  </main>
</div>
</body>
</html>
```